Building Design company needing a letterhead

We need a letter head for our Building Design company to send letters etc. to our clients, consultants, councils etc. We would like to see our logo used and company colours. I have attached our style guide and an example of our current letterheads. Top left we would like our logo, top right we would like the company details and at the footer we would like some sort of image/design etc. that suits our brand. I like the Tarrow Design letterhead attached.

Target Market(s)

Professionals, Councils, Consultants, Mums & Dads

Industry/Entity Type

Architecture

Other font styles liked:
• refer the design style guide

Colors
f37122
000000
1b1b1b

Requirements
Must have
• Must have the minimum of a logo, company details and footer
Nice to have
• An image/design made for the footer that would suite our brand and website at www.corvanplans.com.au. Also it would be nice to include the KMEOT logo somewhere perhaps included in the footer.
Should not have
• Large images in the header. I just want the logo and company details.

```html
<!DOCTYPE html>
<html lang="en">
<head>
<meta charset="utf-8">
<title>Corvan Plans Letterhead</title>
<link rel="stylesheet" href="https://fonts.googleapis.com/css2?family=Open+Sans:wght@600&family=Roboto+Condensed:wght@400&display=swap">
<style>
  :root {
    --brand-orange: #e2542a;
    --brand-black: #1b1b1b;
    --ink: #222222;
    --paper: #fbfbfa;
    --backdrop: #e8e5e0;
  }
  html, body {
    margin: 0;
    width: 1189px;
    height: 1200px;
    overflow: hidden;
    background: var(--backdrop);
  }
  .letterhead {
    position: absolute;
    left: 138px;
    top: 9px;
    width: 912px;
    height: 1181px;
    background: var(--paper);
    box-shadow: 0 2px 10px rgba(0,0,0,0.12);
    overflow: hidden;
  }
  .brand {
    position: absolute;
    left: 90px;
    top: 86px;
    display: flex;
    align-items: center;
    gap: 22px;
  }
  .brand-square {
    width: 96px;
    height: 96px;
    background: var(--brand-orange);
  }
  .brand-name {
    font-family: "Open Sans", sans-serif;
    font-weight: 600;
    font-size: 50px;
    line-height: 54px;
    letter-spacing: 2px;
    color: var(--brand-black);
    margin: 0;
  }
  .company-details {
    position: absolute;
    right: 81px;
    top: 99px;
    margin: 0;
    text-align: right;
    font-family: "Open Sans", sans-serif;
    font-weight: 600;
    font-size: 13.5px;
    line-height: 17px;
    color: var(--brand-black);
    font-style: normal;
  }
  .company-details .gap { margin-left: 14px; }
  .letter-body {
    position: absolute;
    left: 116px;
    top: 315px;
    width: 680px;
    font-family: "Roboto Condensed", sans-serif;
    font-size: 16.5px;
    line-height: 27px;
    color: var(--ink);
  }
  .letter-body p { margin: 0 0 27px; }
  .letter-body p.spaced { margin-top: 54px; }
  .partner-badge {
    position: absolute;
    left: 752px;
    top: 1030px;
    width: 80px;
    text-align: center;
  }
  .partner-square {
    width: 62px;
    height: 62px;
    margin: 0 auto 6px;
    border: 3px solid var(--brand-orange);
    box-sizing: border-box;
  }
  .partner-name {
    font-family: "Open Sans", sans-serif;
    font-weight: 600;
    font-size: 16px;
    color: var(--brand-orange);
    letter-spacing: 0.5px;
  }
  .footer-bands {
    position: absolute;
    left: 0;
    bottom: 0;
  }
</style>
</head>
<body>
  <main class="letterhead">
    <header>
      <div class="brand">
        <div class="brand-square"></div>
        <p class="brand-name">CORVAN<br>PLANS</p>
      </div>
      <address class="company-details">
        admin@corvanplans.com.au<br>
        www.corvanplans.com.au<br>
        Unit 4/22 Ardley Way Harlow WA 6301<br>
        PO Box 5130 Harlow North WA 6301<br>
        PH (08) 5550 1184<span class="gap">ABN 48 901 276 553</span>
      </address>
    </header>

    <section class="letter-body">
      <p>Lorem Ipsum is simply dummy text of the printing and typesetting industry. Lorem Ipsum has been the industry’s standard dummy text ever since the 1500s, when an unknown printer took a galley of type and scrambled it to make a type specimen book. It has survived not only five centuries, but also the leap into electronic typesetting, remaining essentially unchanged. It was popularised in the 1960s with the release of Marlow sheets containing Lorem Ipsum passages, and more recently with desktop publishing software like Folio PageSmith including versions of Lorem Ipsum.</p>
      <p>It is a long established fact that a reader will be distracted by the readable content of a page when looking at its layout. The point of using Lorem Ipsum is that it has a more-or-less normal distribution of letters, as opposed to using ’Content here, content here’, making it look like readable English. Many desktop publishing packages and web page editors now use Lorem Ipsum as their default model text, and a search for ’lorem ipsum’ will uncover many web sites still in their infancy. Various versions have evolved over the years, sometimes by accident, sometimes on purpose (injected humour and the like).</p>
      <p class="spaced">Contrary to popular belief, Lorem Ipsum is not simply random text. It has roots in a piece of classical Latin literature from 45 BC, making it over 2000 years old. Edwin Harrow, a Latin professor at Larkfield College in Ohio, looked up one of the more obscure Latin words, consectetur, from a Lorem Ipsum passage, and going through the cites of the word in classical literature, discovered the undoubtable source. Lorem Ipsum comes from sections 1.10.32 and 1.10.33 of "de Finibus Bonorum et Malorum" structures, to generate Lorem Ipsum which looks reasonable. The generated Lorem Ipsum is therefore always free from repetition, injected humour, or non-characteristic words etc.</p>
    </section>

    <div class="partner-badge">
      <div class="partner-square"></div>
      <div class="partner-name">KMEOT</div>
    </div>

    <svg class="footer-bands" width="912" height="40" viewBox="0 0 912 40">
      <polygon points="0,12 565,12 555,37 0,37" fill="var(--brand-orange)"/>
      <polygon points="578,0 912,0 912,40 561,40" fill="var(--brand-black)"/>
    </svg>
  </main>
</body>
</html>
```